Introduction flyer

Brightpath Dietetics & Vitality Advisory, is a new holistic nutritional therapy specialising in womens health. I want a flyer that appeals to women between 15 to 60. It must speak "health, food & balance". I have attached the basic info I need included in the text. I like Greens & Blues, soft text. My flyer will be distributed to cafes, shops, fitness centres, hung up in grocery stores & health centres etc. The QELR & HPVA logos need to appear on the flyer to show I am fully registered. My own logo & company name is attached.

Target Market(s)

Women from 10 to 60 years old.

Industry/Entity Type

Nutritionist

Colors
32a6d7
abd037
33b8a4
fbf289
ffcf3e
b768aa
d5d5d5
dcdcdc
e8e8e8

Requirements
Must have
• An image of healthy food & ladies. A group of women eating soup, stews or curry type dishes, with plenty of colour - no bread or white wine, and not just fruit please. Food that looks enjoyable to the average person.
• Nutrition is main part of my job, so please keep that in mind & emphasise food & natural well being.
Should not have
• People exercising, men, white wine, bread, cakes, sweets etc..

```html
<!DOCTYPE html>
<html lang="en">
<head>
<meta charset="utf-8">
<title>Brightpath Dietetics – Introduction Flyer</title>
<link href="https://fonts.googleapis.com/css2?family=Open+Sans:wght@400;600;700;800&family=Oswald:wght@600;700&display=swap" rel="stylesheet">
<style>
:root{
  --green:#1f8f3e;
  --green-deep:#137a34;
  --blue:#2f6db5;
  --blue-band:#3c78bd;
  --teal:#1e9bb5;
  --charcoal:#272d2b;
  --panel-grey:#eceeee;
  --text:#333a3a;
  --rule:#9aa3a3;
  --white:#ffffff;
  --stage:#e8e8e8;
}
*{margin:0;padding:0;box-sizing:border-box}
html,body{width:1028px;height:1200px;overflow:hidden;background:var(--stage);font-family:"Open Sans",Arial,sans-serif;color:var(--text)}
.flyer{position:absolute;left:89px;top:0;width:850px;height:1200px;background:var(--white);overflow:hidden}
.block{position:absolute}
.photo-basket{left:0;top:0;width:529px;height:417px;background:radial-gradient(ellipse at 55% 60%,#b7c24a 0%,#c0472b 35%,#5a2a14 65%,#120d08 100%)}
.photo-lunch{left:540px;top:0;width:310px;height:263px;background:linear-gradient(180deg,#6f8a4e 0%,#a3b37a 40%,#e96b9c 75%,#d94b87 100%)}
.photo-berries{left:540px;top:273px;width:149px;height:144px;background:linear-gradient(160deg,#f1efee 0%,#dfe2de 60%,#8e2438 100%)}
.photo-veg{left:700px;top:273px;width:150px;height:144px;background:linear-gradient(135deg,#3f7a2e 0%,#e06a26 45%,#c9242e 75%,#f2f2ee 100%)}
.brand{position:absolute;left:40px;top:30px;width:190px;text-align:center;color:var(--white)}
.brand-mark{display:inline-block;width:16px;height:16px;border-radius:50%;background:var(--white);margin-bottom:40px}
.brand-name{font-size:11.5px;font-weight:600;letter-spacing:.4px;line-height:1.25}
.headline{left:44px;top:426px;width:800px;color:var(--green);line-height:1}
.headline .l1{font-size:45px;font-weight:400;letter-spacing:-.3px}
.headline .l1 .soft{color:var(--blue)}
.headline .l1 b{font-weight:800}
.headline .l2{font-size:27px;margin-top:8px}
.headline .l2 b{color:var(--blue);font-weight:700}
.headline .l3{font-size:33px;margin-top:10px}
.headline b{font-weight:700}
.intro{left:0;top:573px;width:548px;height:323px;background:var(--panel-grey);padding:24px 20px 0 29px}
.intro h2{font-size:23px;font-weight:700;color:var(--green);line-height:1.47;letter-spacing:.2px}
.intro h2 .blue{color:var(--blue)}
.intro p{margin-top:18px;font-size:15.5px;line-height:1.5;padding-left:6px;width:490px}
.quote{left:0;top:896px;width:548px;height:65px;background:var(--teal);color:var(--white);text-align:center;font-weight:700;font-size:21px;line-height:1.5}
.checks{left:0;top:961px;width:548px;height:223px}
.checks ul{position:absolute;top:16px;list-style:none;font-size:13.5px;line-height:1.32}
.checks .col-a{left:33px;width:232px}
.checks .col-b{left:296px;width:248px}
.checks .divider{position:absolute;left:270px;top:20px;width:1px;height:186px;background:var(--rule)}
.checks li{position:relative;padding-left:31px;margin-bottom:9px}
.checks .col-b li{padding-left:33px;margin-bottom:8px}
.checks svg{position:absolute;left:0;top:3px;width:11px;height:11px}
.bottom-strip{left:0;top:1185px;width:548px;height:15px;background:var(--blue-band)}
.home-visits{left:548px;top:573px;width:302px;height:75px;background:var(--blue-band);color:var(--white);font-weight:700;font-size:14.5px;line-height:1.45;padding:7px 14px 0 20px}
.call{left:548px;top:648px;width:302px;height:90px;background:var(--charcoal);color:var(--white);font-family:"Oswald",Impact,sans-serif;font-weight:700;padding:4px 0 0 27px;line-height:1.12}
.call .today{font-size:35px;letter-spacing:.5px}
.call .phone{font-size:35px;display:flex;align-items:center;gap:6px;margin-left:-4px}
.call svg{width:30px;height:30px}
.email{left:548px;top:738px;width:302px;height:31px;background:var(--blue-band);color:var(--white);font-weight:700;font-size:14.5px;padding:5px 0 0 28px}
.booking{left:548px;top:769px;width:302px;height:431px;background:linear-gradient(160deg,#1f9a45 0%,var(--green-deep) 70%,#0f6a2c 100%);color:var(--white);padding:12px 14px 0 20px}
.booking .lead{font-size:18px;line-height:1.2}
.booking .big{font-size:30px;line-height:1.2}
.booking .huge{font-size:31px;font-weight:800;line-height:1.17}
.booking .huge2{font-size:37px;font-weight:800;line-height:1.12}
.booking b{font-weight:800}
.booking p{font-size:12.5px;line-height:1.4;margin-top:8px}
.booking p + p{margin-top:10px}
.members{left:548px;top:1066px;width:302px;height:85px;background:var(--white);display:flex;align-items:center;justify-content:space-around;padding:0 10px}
.member{display:flex;align-items:center;gap:7px;font-weight:800;font-size:26px}
.member .dot{width:22px;height:22px;border-radius:50%}
.member-hpva{color:var(--green)}
.member-hpva .dot{background:var(--teal)}
.member-qelr{color:#5b3c8e}
.member-qelr .dot{background:#5b3c8e}
</style>
</head>
<body>
<main class="flyer">
  <div class="block photo-basket" role="img" aria-label="Wicker basket of apples, pears, oranges, strawberries and green grapes on a dark background"></div>
  <div class="brand">
    <span class="brand-mark"></span>
    <div class="brand-name">Brightpath Dietetics<br>&amp; Vitality Advisory</div>
  </div>
  <div class="block photo-lunch" role="img" aria-label="Three women sharing colourful dishes at a low table on a pink picnic blanket outdoors"></div>
  <div class="block photo-berries" role="img" aria-label="Glass of yoghurt with falling blackberries and redcurrants"></div>
  <div class="block photo-veg" role="img" aria-label="Fresh carrots, strawberries, tomatoes, walnuts and leafy greens"></div>

  <header class="block headline">
    <div class="l1"><span class="soft">DO YOU</span> <b>EXPERIENCE LOW ENERGY,</b></div>
    <div class="l2">LOW LIBIDO, <b>MENSTRUAL CYCLE COMPLICATIONS</b>,</div>
    <div class="l3">OR ARE YOU PLANNING <b>A BABY?</b></div>
  </header>

  <section class="block intro">
    <h2>SMALL CHANGES TO YOUR DIET MAY<br>LEAD TO BIG CHANGES IN YOUR HEALTH.<br><span class="blue">EAT WELL, LIVE WELL.</span></h2>
    <p>Discover exactly what YOU need to change and how to make these changes long lasting.<br>There is no one-rule-fits-all. My nutritional advice aims to dig up the root cause to my client's health concerns. My lifestyle plans are completely personalised to an individual's needs and circumstances. I consider the whole person not just symptoms or disease.</p>
  </section>

  <div class="block quote">"Empowering women to take control of<br>their own health”</div>

  <section class="block checks">
    <ul class="col-a">
      <li><svg viewBox="0 0 12 12"><rect x=".5" y=".5" width="11" height="11" fill="none" stroke="#1f8f3e"/><path d="M2.5 6l2.5 2.5L10 2.5" fill="none" stroke="#1f8f3e" stroke-width="1.6"/></svg>Fertility, IVF, pre-conception, pregnancy &amp; post-natal care</li>
      <li><svg viewBox="0 0 12 12"><rect x=".5" y=".5" width="11" height="11" fill="none" stroke="#1f8f3e"/><path d="M2.5 6l2.5 2.5L10 2.5" fill="none" stroke="#1f8f3e" stroke-width="1.6"/></svg>Menstrual cycle challenges (PCOS, Endometriosis, PMS, heavy/irregular periods etc)</li>
      <li><svg viewBox="0 0 12 12"><rect x=".5" y=".5" width="11" height="11" fill="none" stroke="#1f8f3e"/><path d="M2.5 6l2.5 2.5L10 2.5" fill="none" stroke="#1f8f3e" stroke-width="1.6"/></svg>Thyroid conditions</li>
      <li><svg viewBox="0 0 12 12"><rect x=".5" y=".5" width="11" height="11" fill="none" stroke="#1f8f3e"/><path d="M2.5 6l2.5 2.5L10 2.5" fill="none" stroke="#1f8f3e" stroke-width="1.6"/></svg>Low libido</li>
    </ul>
    <span class="divider"></span>
    <ul class="col-b">
      <li><svg viewBox="0 0 12 12"><rect x=".5" y=".5" width="11" height="11" fill="none" stroke="#1f8f3e"/><path d="M2.5 6l2.5 2.5L10 2.5" fill="none" stroke="#1f8f3e" stroke-width="1.6"/></svg>Digestive health</li>
      <li><svg viewBox="0 0 12 12"><rect x=".5" y=".5" width="11" height="11" fill="none" stroke="#1f8f3e"/><path d="M2.5 6l2.5 2.5L10 2.5" fill="none" stroke="#1f8f3e" stroke-width="1.6"/></svg>Chronic fatigue syndrome</li>
      <li><svg viewBox="0 0 12 12"><rect x=".5" y=".5" width="11" height="11" fill="none" stroke="#1f8f3e"/><path d="M2.5 6l2.5 2.5L10 2.5" fill="none" stroke="#1f8f3e" stroke-width="1.6"/></svg>Perimenopause/menopause</li>
      <li><svg viewBox="0 0 12 12"><rect x=".5" y=".5" width="11" height="11" fill="none" stroke="#1f8f3e"/><path d="M2.5 6l2.5 2.5L10 2.5" fill="none" stroke="#1f8f3e" stroke-width="1.6"/></svg>Weight management</li>
      <li><svg viewBox="0 0 12 12"><rect x=".5" y=".5" width="11" height="11" fill="none" stroke="#1f8f3e"/><path d="M2.5 6l2.5 2.5L10 2.5" fill="none" stroke="#1f8f3e" stroke-width="1.6"/></svg>Type 2 diabetes, blood sugar dysregulation, high blood pressure, high cholesterol</li>
    </ul>
  </section>
  <div class="block bottom-strip"></div>

  <div class="block home-visits">Home visits available, at no extra cost within local area; I can visit your place of work or home.</div>
  <div class="block call">
    <div class="today">TODAY ON</div>
    <div class="phone"><svg viewBox="0 0 24 24"><path d="M6.6 3.5l2.6 3.2-1.6 2.2c1.2 2.6 3 4.4 5.5 5.6l2.2-1.6 3.2 2.6-1.4 3c-6.8-.4-12-5.6-12.4-12.4z" fill="none" stroke="#fff" stroke-width="1.6" stroke-linejoin="round"/></svg>087-4402-519</div>
  </div>
  <div class="block email">hello@brightpathdietetics.ie</div>

  <section class="block booking">
    <div class="lead"><b>Book A</b> Consultation Or For A</div>
    <div class="big"><b>free</b> no obligation</div>
    <div class="huge">15-minute mini</div>
    <div class="huge2">consultation.</div>
    <p>Initial consultations typically last up to 2 hours, follow-ups 30 – 60 minutes.</p>
    <p>An in-depth case history is gathered during the initial consultation. This includes all aspects of your lifestyle both past and present, from what you eat to how you sleep.</p>
  </section>

  <div class="block members">
    <div class="member member-hpva"><span class="dot"></span>HPVA</div>
    <div class="member member-qelr"><span class="dot"></span>QELR</div>
  </div>
</main>
</body>
</html>
```